Sales Flyer for Outdoor Kitchens

Looks to have a trifold flyer designed based off website content / projects. Use www.backyardhearthworks.com for content

```html
<!DOCTYPE html>
<html lang="en">
<head>
<meta charset="UTF-8">
<title>Backyard Hearthworks – Outdoor Kitchens Flyer</title>
<link href="https://fonts.googleapis.com/css2?family=Poppins:wght@500;600;700;800&display=swap" rel="stylesheet">
<style>
  :root {
    --stage: #d9e3ea;
    --paper: #ffffff;
    --brand-green: #33a83b;
    --brand-blue: #1f6bb5;
    --ink: #111111;
    --photo-leaf: #4f8a3a;
    --photo-wood: #8a5a32;
    --photo-stone: #c9c4b8;
  }
  * { margin: 0; padding: 0; box-sizing: border-box; }
  html, body {
    width: 1200px; height: 900px; overflow: hidden;
    background: var(--stage);
    font-family: "Poppins", sans-serif;
  }
  .flyer-panel {
    position: absolute;
    left: 400px; top: 20px;
    width: 400px; height: 860px;
    background: var(--paper);
    overflow: hidden;
    box-shadow: 0 6px 24px rgba(0,0,0,0.15);
  }
  .brand-header {
    position: absolute; left: 0; top: 34px; width: 100%;
    display: flex; align-items: center; justify-content: center; gap: 10px;
  }
  .brand-dot {
    width: 22px; height: 22px; border-radius: 50%;
    background: var(--brand-green);
  }
  .brand-name {
    font-weight: 700; font-size: 24px; letter-spacing: 0.5px;
    color: var(--brand-green); text-transform: uppercase;
  }
  .hero-art { position: absolute; left: 0; top: 0; width: 400px; height: 600px; }
  .cta-block {
    position: absolute; left: 0; top: 600px; width: 100%;
    text-align: center; padding: 0 22px;
  }
  .cta-kicker {
    display: flex; align-items: center; justify-content: center; gap: 8px;
    font-weight: 600; font-size: 13px; letter-spacing: 1px;
    color: var(--brand-blue); text-transform: uppercase;
  }
  .cta-kicker::before, .cta-kicker::after {
    content: ""; width: 40px; height: 2px; background: var(--brand-blue);
  }
  .cta-headline {
    margin-top: 8px;
    font-weight: 800; font-size: 31px; line-height: 1.08;
    color: var(--ink); text-transform: uppercase;
  }
  .cta-headline .accent { color: var(--brand-green); }
  .phone-pill {
    margin: 16px auto 0; width: 330px; height: 54px;
    background: var(--brand-blue); border-radius: 27px;
    display: flex; align-items: center; gap: 14px; padding-left: 8px;
  }
  .phone-icon {
    width: 40px; height: 40px; border-radius: 50%;
    background: var(--brand-green);
    display: flex; align-items: center; justify-content: center;
  }
  .phone-number {
    font-weight: 700; font-size: 30px; letter-spacing: 1.5px; color: var(--paper);
  }
  .site-url {
    margin-top: 8px; font-weight: 500; font-size: 15px; color: var(--ink);
  }
</style>
</head>
<body>
  <main class="flyer-panel">
    <svg class="hero-art" viewBox="0 0 400 600" xmlns="http://www.w3.org/2000/svg">
      <defs>
        <linearGradient id="photoTone" x1="0" y1="0" x2="1" y2="1">
          <stop offset="0" stop-color="var(--photo-wood)"/>
          <stop offset="0.45" stop-color="var(--photo-leaf)"/>
          <stop offset="1" stop-color="var(--photo-stone)"/>
        </linearGradient>
      </defs>
      <path class="blue-swoosh" d="M400 420 L400 560 C340 590 270 600 200 598 C300 560 360 500 400 420 Z" fill="var(--brand-blue)"/>
      <path role="img" aria-label="Photo of a timber-framed outdoor pavilion with a fire table, lounge chairs and a brick outdoor kitchen among trees"
            d="M0 170 C120 170 260 150 400 80 L400 420 C360 510 290 575 180 588 C110 596 50 598 0 600 Z"
            fill="url(#photoTone)"/>
      <path class="green-rule" d="M0 170 C120 170 260 150 400 80" fill="none" stroke="var(--brand-green)" stroke-width="5"/>
    </svg>

    <header class="brand-header">
      <span class="brand-dot"></span>
      <span class="brand-name">Backyard Hearthworks</span>
    </header>

    <section class="cta-block">
      <p class="cta-kicker">Backyard Hearthworks</p>
      <h1 class="cta-headline">Create <span class="accent">Your Dream</span><br>Backyard With Us</h1>
      <div class="phone-pill">
        <span class="phone-icon">
          <svg width="22" height="22" viewBox="0 0 24 24" aria-hidden="true">
            <path d="M6.6 10.8a15.1 15.1 0 0 0 6.6 6.6l2.2-2.2a1 1 0 0 1 1-.25 11.4 11.4 0 0 0 3.6.57 1 1 0 0 1 1 1V20a1 1 0 0 1-1 1A17 17 0 0 1 3 4a1 1 0 0 1 1-1h3.5a1 1 0 0 1 1 1c0 1.25.2 2.45.57 3.57a1 1 0 0 1-.25 1z" fill="#ffffff"/>
          </svg>
        </span>
        <span class="phone-number">555-014-2290</span>
      </div>
      <p class="site-url">www.backyardhearthworks.com</p>
    </section>
  </main>
</body>
</html>
```